A website for a Maltese Law Firm

Our law firm needs a website to further its business. The site should have a simple yet effective design. We would need the following sections: About us, Practice Areas, About Malta, Contact. These should be further split as follows:

About us: Our firm, Our values, What others say, Offices

Practice Areas: Crimimal, Citizenship & Residence, Sovereign Patron Pathway, Criminal Defence, Civil Litigation, Arbitration and ADR, Commercial and Corporate, Media Law.

About Malta: just one section.

Contact: Just one section

We would also need a news feed at the front of the site to include latest news regarding our cases.

At the bottom we need a section for our Terms and a Privacy Statement.

Our logo is being attached.

Target Market(s)

All clients looking for legal assistance in Malta

Industry/Entity Type

Legal

Coding

Coded - Design and coding required

Number of Pages Required

1 page

Requirements
Must have
• It must be simple yet striking.

```html
<!DOCTYPE html>
<html lang="en">
<head>
<meta charset="utf-8">
<title>Verdala &amp; Kordin Advocates</title>
<link href="https://fonts.googleapis.com/css2?family=Open+Sans:ital,wght@0,400;0,600;0,700;1,400&family=Raleway:wght@400;500;600;700&family=Roboto+Slab:wght@300;400&display=swap" rel="stylesheet">
<style>
:root{
  --ink:#222;
  --text:#333;
  --muted:#666;
  --line:#cfcfcf;
  --topbar:#1b1b1b;
  --panel:#333333;
  --field:#666666;
  --soft:#f5f5f5;
  --band:#9a9a9a;
  --footer:#1f1f1f;
  --footer-base:#0d0d0d;
  --white:#fff;
  --date:#8d8d8d;
}
*{box-sizing:border-box;margin:0;padding:0}
html,body{width:1200px;height:2493px;overflow:hidden}
body{position:relative;background:var(--white);font-family:"Open Sans",Arial,sans-serif;color:var(--text)}
.abs{position:absolute}
.heading{font-family:"Raleway",Arial,sans-serif;font-weight:500;color:var(--ink)}

/* top bar */
.topbar{left:0;top:0;width:1200px;height:37px;background:var(--topbar)}
.social{display:flex;gap:8px}
.social span{width:19px;height:19px;border:1px solid #bbb;display:block}
.top-social{left:83px;top:9px}
.consult{left:462px;top:0;width:278px;height:44px;background:var(--white);border:1px solid #bbb;border-top:none;font-family:"Raleway",sans-serif;font-size:16px;color:#333;display:flex;align-items:center;justify-content:center;box-shadow:0 1px 3px rgba(0,0,0,.2)}
.contact-top{top:8px;color:#ddd;font-size:13px;display:flex;align-items:center;gap:10px}
.contact-top .ico{width:22px;height:20px;border:1px solid #bbb;display:flex;align-items:center;justify-content:center}

/* header */
.brand{left:83px;top:68px;font-family:"Raleway",sans-serif;font-weight:600;font-size:25px;letter-spacing:.3px;color:#222;line-height:34px}
.nav{left:404px;top:86px;display:flex;font-family:"Raleway",sans-serif;font-size:14px;color:#777}
.nav a{color:inherit;text-decoration:none;padding:0 12px;border-left:1px solid #ccc;line-height:20px}
.nav a:first-child{border-left:none;padding-left:0;color:#222}

/* hero */
.hero{left:0;top:133px;width:1200px;height:507px;background:radial-gradient(ellipse at 45% 40%,#a8763a 0%,#6e4520 45%,#2e1a0c 100%)}
.hero-caption{left:96px;top:329px;width:541px;height:115px;background:rgba(20,18,16,.75);color:#fff;font-family:"Raleway",sans-serif;font-size:29px;line-height:42px;padding:15px 28px}
.arrow{width:30px;height:30px;border-radius:50%;background:#fff;display:flex;align-items:center;justify-content:center}

/* about */
.about-title{left:83px;top:700px;width:697px;font-size:27px;padding-bottom:8px;border-bottom:1px solid var(--line)}
.about-text{left:83px;top:752px;width:660px;font-size:12px;line-height:20px;color:#333}
.btn-dark{background:#111;color:#fff;font-family:"Raleway",sans-serif;font-weight:700;font-size:14px;display:flex;align-items:center;justify-content:center}
.feature{top:924px;width:221px;height:86px;border:1px solid var(--line);display:flex;gap:12px;padding:14px 12px}
.feature .icon{width:60px;height:52px;background:#5a5a5a;border-radius:3px;flex:none}
.feature h4{font-family:"Raleway",sans-serif;font-weight:500;font-size:16px;color:#333;margin-bottom:4px}
.feature p{font-size:12px;line-height:17px;color:#444}

.form{left:813px;top:685px;width:302px;height:324px;background:var(--panel);padding:14px 15px;box-shadow:0 1px 4px rgba(0,0,0,.3)}
.form h3{font-family:"Raleway",sans-serif;font-weight:500;font-size:19px;line-height:23px;color:#fff;margin-bottom:12px}
.form .field{background:var(--field);color:#eee;font-size:12px;height:37px;padding:10px 13px;margin:0 0 8px 0}
.form .field.msg{height:62px}
.form .submit{width:104px;height:31px;margin-top:4px}

/* practice */
.practice{left:0;top:1064px;width:1200px;height:724px;background:var(--soft)}
.practice-title{left:0;top:1108px;width:1200px;text-align:center;font-size:26px}
.practice-title span{display:inline-block;border-bottom:1px solid #999;padding-bottom:4px}
.tile{width:254px;height:220px}
.tile-label{width:254px;text-align:center;font-family:"Raleway",sans-serif;font-weight:700;font-size:15px;color:#222}

/* cta */
.cta{left:0;top:1788px;width:1200px;height:60px;background:var(--band);color:#fff;font-family:"Roboto Slab","Raleway",serif;font-weight:400;font-size:30px;display:flex;align-items:center;justify-content:center}

/* news & testimonials */
.col-title{top:1900px;font-size:27px;padding-bottom:10px;border-bottom:1px solid var(--line);display:flex;justify-content:space-between;align-items:flex-end}
.col-title small{font-size:18px;color:#222;letter-spacing:2px}
.case{left:86px;width:486px;display:flex;gap:16px}
.date{width:44px;flex:none;text-align:center}
.date .d{background:var(--date);color:#fff;font-size:15px;height:36px;line-height:36px}
.date .m{background:#111;color:#fff;font-size:11px;font-weight:700;height:27px;line-height:27px}
.case h5{font-size:13px;font-weight:700;color:#111;margin:-2px 0 6px}
.case p{font-size:12px;line-height:20px;color:#333}
.quote{left:602px;top:1961px;width:515px;height:150px;border:1px solid var(--line);padding:14px 22px 0 45px;font-style:italic;font-size:12px;line-height:21px;color:#333}
.qmark{font-family:Georgia,serif;font-size:40px;color:#ccc;font-style:normal;line-height:1}
.avatar{left:602px;top:2131px;width:50px;height:51px;background:linear-gradient(#c9c9c9,#8a8a8a)}
.client{left:664px;top:2147px;font-size:14px;font-weight:700;color:#222}

/* footer */
.footer{left:0;top:2224px;width:1200px;height:241px;background:var(--footer)}
.foot-base{left:0;top:2465px;width:1200px;height:28px;background:var(--footer-base);color:#ddd;font-size:11px;text-align:center;line-height:28px}
.foot-h{font-family:"Raleway",sans-serif;font-size:15px;color:#eee}
.links{list-style:none;font-size:12px;color:#ddd;line-height:22px}
.links li::before{content:"›";color:#888;margin-right:12px}
.divider{top:2254px;width:1px;height:180px;background:#3a3a3a}
.contact-row{display:flex;gap:10px;color:#ddd;font-size:12px;line-height:17px;align-items:flex-start}
.contact-row .ico{width:16px;height:16px;border:1px solid #bbb;flex:none;display:flex;align-items:center;justify-content:center;margin-top:1px}
.map{left:587px;top:2254px;width:264px;height:170px;background:linear-gradient(135deg,#e8e4dc 0%,#dcd8cf 55%,#9fc0e0 70%,#aac8e6 100%);border:3px solid #555}
.foot-brand{left:902px;top:2305px;width:212px;text-align:center;font-family:"Raleway",sans-serif;font-weight:600;font-size:19px;color:#aaa}
.follow{left:920px;top:2358px;display:flex;gap:10px;align-items:center;color:#ddd;font-size:12px}
.follow .social span{border-color:#ddd;width:20px;height:20px}
</style>
</head>
<body>

<!-- top bar -->
<div class="abs topbar"></div>
<div class="abs social top-social"><span></span><span></span><span></span><span></span></div>
<div class="abs consult">Schedule Free Consultation</div>
<div class="abs contact-top" style="left:786px">
  <span class="ico"><svg width="12" height="12" viewBox="0 0 24 24"><path fill="#ddd" d="M6.6 10.8a15 15 0 006.6 6.6l2.2-2.2c.3-.3.7-.4 1-.2 1.1.4 2.3.6 3.6.6.6 0 1 .4 1 1V20c0 .6-.4 1-1 1A17 17 0 013 4c0-.6.4-1 1-1h3.5c.6 0 1 .4 1 1 0 1.3.2 2.5.6 3.6.1.3 0 .7-.2 1z"/></svg></span>356 2000 1140
</div>
<div class="abs contact-top" style="left:926px">
  <span class="ico"><svg width="12" height="10" viewBox="0 0 24 18"><rect x="1" y="1" width="22" height="16" fill="#ddd"/><path d="M1 1l11 9 11-9" stroke="#1b1b1b" stroke-width="2" fill="none"/></svg></span>hello@verdalakordin.com
</div>

<!-- header -->
<div class="abs brand">Verdala &amp; Kordin</div>
<nav class="abs nav">
  <a>HOME</a><a>ABOUT US</a><a>OUR FIRM</a><a>OUR VALUES</a><a>WHAT OTHERS SAY</a><a>OFFICES</a><a>CONTACT US</a>
</nav>

<!-- hero -->
<div class="abs hero" role="img" aria-label="Photo of a judge's gavel, handcuffs and open law books on a wooden desk"></div>
<div class="abs hero-caption">Get Qualified Legal Advice In Malta<br>For Criminal Law</div>
<div class="abs arrow" style="left:54px;top:371px"><svg width="10" height="12" viewBox="0 0 10 12"><path d="M7 1L2 6l5 5" stroke="#222" stroke-width="2" fill="none"/></svg></div>
<div class="abs arrow" style="left:1117px;top:371px"><svg width="10" height="12" viewBox="0 0 10 12"><path d="M3 1l5 5-5 5" stroke="#222" stroke-width="2" fill="none"/></svg></div>

<!-- about -->
<h2 class="abs heading about-title">About Verdala &amp; Kordin Advocates</h2>
<p class="abs about-text">Lorem ipsum dolor sit amet, consectetuer adipiscing elit, sed diam nonummy nibh euismod tincidunt ut laoreet dolore magna aliquam erat volutpat. Ut wisi enim ad minim veniam, quis nostrud exerci tation ullamcorper suscipit lobortis nisl ut aliquip ex ea commodo consequat. Duis autem vel eum iriure dolor in hendrerit in vulputate velit esse molestie consequat, vel illum dolore eu feugiat nulla facilisis at vero eros et accumsan et iusto odio dignissim qui blandit praesent luptatum zzril delenit augue duis dolore te feugait nulla facilisi.</p>
<div class="abs btn-dark" style="left:83px;top:866px;width:103px;height:29px">Read More</div>

<div class="abs feature" style="left:83px"><div class="icon" role="img" aria-label="Scales of justice icon"></div><div><h4>Our Firm</h4><p>Lorem ipsum dolor sit consectetuer adipiscn</p></div></div>
<div class="abs feature" style="left:322px"><div class="icon" role="img" aria-label="Handshake icon"></div><div><h4>Our Values</h4><p>Lorem ipsum dolor sit consectetuer adipiscn</p></div></div>
<div class="abs feature" style="left:560px"><div class="icon" role="img" aria-label="Maltese church buildings icon"></div><div><h4>About Malta</h4><p>Lorem ipsum dolor sit consectetuer adipiscn</p></div></div>

<form class="abs form">
  <h3>Request for Free<br>Consulatation</h3>
  <div class="field">Name</div>
  <div class="field">Email</div>
  <div class="field">Inquiry Tpye</div>
  <div class="field msg">Message</div>
  <div class="btn-dark submit">SUBMIT</div>
</form>

<!-- practice areas -->
<section class="abs practice"></section>
<h2 class="abs heading practice-title"><span>Our Practice Areas</span></h2>

<div class="abs tile" style="left:83px;top:1188px;background:linear-gradient(135deg,#8a4a22,#d9c7a8 60%,#6b3a1c)" role="img" aria-label="Gavel on a criminal law document"></div>
<div class="abs tile" style="left:344px;top:1188px;background:linear-gradient(135deg,#1c2545,#2f3a66 60%,#121830)" role="img" aria-label="Close-up of a passport cover"></div>
<div class="abs tile" style="left:603px;top:1188px;background:linear-gradient(135deg,#7fa3c9,#e9eef3 60%,#c9d3dc)" role="img" aria-label="Businessman signing a document"></div>
<div class="abs tile" style="left:863px;top:1188px;background:linear-gradient(135deg,#dfe9f1,#8fb0c9 50%,#2c3e52)" role="img" aria-label="Contract and pen with business people in silhouette"></div>
<div class="abs tile-label" style="left:83px;top:1427px">Crimimal</div>
<div class="abs tile-label" style="left:344px;top:1427px">Citizenship &amp; Residence</div>
<div class="abs tile-label" style="left:603px;top:1427px">Sovereign Patron Pathway</div>
<div class="abs tile-label" style="left:863px;top:1427px">Commercial &amp; Corporate</div>

<div class="abs tile" style="left:83px;top:1496px;background:linear-gradient(135deg,#2f3136,#5c6067 55%,#a8aaa6)" role="img" aria-label="Person in handcuffs"></div>
<div class="abs tile" style="left:344px;top:1496px;background:linear-gradient(135deg,#111,#5a2a16 60%,#b88a3c)" role="img" aria-label="Scales of justice and books for civil litigation"></div>
<div class="abs tile" style="left:603px;top:1496px;background:linear-gradient(135deg,#2a3b57,#7b98bd 50%,#2a2f3b)" role="img" aria-label="Business people meeting in a boardroom"></div>
<div class="abs tile" style="left:863px;top:1496px;background:linear-gradient(135deg,#e0ddd6,#8a4a1e 55%,#3c1d0b)" role="img" aria-label="Gavel beside a keyboard"></div>
<div class="abs tile-label" style="left:83px;top:1740px">Criminal Defence</div>
<div class="abs tile-label" style="left:344px;top:1740px">Civil Litigation</div>
<div class="abs tile-label" style="left:603px;top:1740px">Arbitration &amp; ADR</div>
<div class="abs tile-label" style="left:863px;top:1740px">Media Law</div>

<!-- call to action -->
<div class="abs cta">Call Us 356 2000 1140&nbsp; At&nbsp; Or Contact Us Online For A Free Estimate</div>

<!-- recent case studies -->
<h2 class="abs heading col-title" style="left:83px;width:489px">Recent Case Studies <small>‹ ›</small></h2>
<article class="abs case" style="top:1961px"><div class="date"><div class="d">23</div><div class="m">MAR</div></div><div><h5>Lorem Ispum the dunny rect</h5><p>Lorem ipsum dolor sit amet, consectetuer adipiscing elit, sed diam nonummy nibh euismod tincidunt ut laoreet dolore magna</p></div></article>
<article class="abs case" style="top:2041px"><div class="date"><div class="d">23</div><div class="m">MAR</div></div><div><h5>Lorem Ispum the dunny rect</h5><p>Lorem ipsum dolor sit amet, consectetuer adipiscing elit, sed diam nonummy nibh euismod tincidunt ut laoreet dolore magna</p></div></article>
<article class="abs case" style="top:2121px"><div class="date"><div class="d">23</div><div class="m">MAR</div></div><div><h5>Lorem Ispum the dunny rect</h5><p>Lorem ipsum dolor sit amet, consectetuer adipiscing elit, sed diam nonummy nibh euismod tincidunt ut laoreet dolore magna</p></div></article>

<!-- testimonials -->
<h2 class="abs heading col-title" style="left:602px;width:515px">Client Testimonials <small>‹ ›</small></h2>
<blockquote class="abs quote"><span class="abs qmark" style="left:14px;top:8px">“</span>Lorem ipsum dolor sit amet, consectetuer adipiscing elit, sed diam nonummy nibh euismod tincidunt ut laoreet dolore magna aliquam erat volutpat. Ut wisi enim ad minim veniam, quis nostrud exerci tation ullamcorper suscipit lobortis nisl ut aliquip ex ea commodo consequat. Duis autem vel eum iriure dolor in hendrerit in vulputate velit esse molestie consequat, vel illum dolore eu feugiat <span class="qmark" style="font-size:30px;vertical-align:-12px">”</span></blockquote>
<div class="abs avatar" role="img" aria-label="Client portrait"></div>
<div class="abs client">Mark Derby</div>

<!-- footer -->
<footer class="abs footer"></footer>
<div class="abs foot-h" style="left:90px;top:2248px">Quick Links</div>
<ul class="abs links" style="left:84px;top:2290px">
  <li>Home</li><li>About Us</li><li>Our Firm</li><li>Our Values</li><li>What Others Say</li><li>Offices</li><li>Contact Us</li>
</ul>
<div class="abs divider" style="left:275px"></div>
<div class="abs foot-h" style="left:311px;top:2250px">Contact Details</div>
<div class="abs contact-row" style="left:306px;top:2291px"><span class="ico"><svg width="8" height="11" viewBox="0 0 8 11"><path d="M4 0a4 4 0 00-4 4c0 3 4 7 4 7s4-4 4-7a4 4 0 00-4-4z" fill="#ddd"/><circle cx="4" cy="4" r="1.4" fill="#1f1f1f"/></svg></span><span>12/4, Merchant Lane, Valletta<br>88, Olive Grove Street, Birkirkara</span></div>
<div class="abs contact-row" style="left:306px;top:2340px"><span class="ico"><svg width="9" height="9" viewBox="0 0 24 24"><path fill="#ddd" d="M6.6 10.8a15 15 0 006.6 6.6l2.2-2.2c.3-.3.7-.4 1-.2 1.1.4 2.3.6 3.6.6.6 0 1 .4 1 1V20c0 .6-.4 1-1 1A17 17 0 013 4c0-.6.4-1 1-1h3.5c.6 0 1 .4 1 1 0 1.3.2 2.5.6 3.6.1.3 0 .7-.2 1z"/></svg></span><span>356 2000 1140 ( Valletta )</span></div>
<div class="abs contact-row" style="left:306px;top:2372px"><span class="ico"><svg width="9" height="9" viewBox="0 0 24 24"><path fill="#ddd" d="M6.6 10.8a15 15 0 006.6 6.6l2.2-2.2c.3-.3.7-.4 1-.2 1.1.4 2.3.6 3.6.6.6 0 1 .4 1 1V20c0 .6-.4 1-1 1A17 17 0 013 4c0-.6.4-1 1-1h3.5c.6 0 1 .4 1 1 0 1.3.2 2.5.6 3.6.1.3 0 .7-.2 1z"/></svg></span><span>356 2000 1177 (Birkirkara )</span></div>
<div class="abs contact-row" style="left:306px;top:2402px"><span class="ico"><svg width="10" height="8" viewBox="0 0 24 18"><rect x="1" y="1" width="22" height="16" fill="#ddd"/><path d="M1 1l11 9 11-9" stroke="#1f1f1f" stroke-width="2" fill="none"/></svg></span><span>hello@verdalakordin.com</span></div>
<div class="abs divider" style="left:548px"></div>
<div class="abs map" role="img" aria-label="Map of Malta showing Valletta and Birkirkara"></div>
<div class="abs divider" style="left:878px"></div>
<div class="abs foot-brand">Verdala &amp; Kordin</div>
<div class="abs follow">Follow us <div class="social"><span></span><span></span><span></span><span></span></div></div>
<div class="abs foot-base">Copyright © 2016 Verdala &amp; Kordin Advocates. All rights reserved.</div>

</body>
</html>
```